BOLD & MINIMALIST DESIGN NEEDED

We want a very bold but minimalistic business card design that is impactful and utilizes both sides of the business card. Our current logo is included for your use.

We want bold fonts and good use of negative space. We don't want the logo to overpower the design.

Target Market(s)

Professionals who are building new commercial buildings.

Industry/Entity Type

Construction

Contact Information for Business Card

Name, Title, email, office phone, cell phone, website

Font styles to use
Serif
Sans Serif

Requirements
Must have
• Bold design!

```html
<!DOCTYPE html>
<html lang="en">
<head>
<meta charset="utf-8">
<title>Ridgemont Build — Business Card</title>
<link rel="stylesheet" href="https://fonts.googleapis.com/css2?family=Poppins:wght@400;600;700;800&display=swap">
<style>
  :root {
    --backdrop: #262626;
    --card-dark: #1f1f1f;
    --card-dark-edge: #2c2c2c;
    --card-light: #f1f1f0;
    --ink: #1c1c1c;
    --ink-soft: #2a2a2a;
    --accent: #7ab829;
    --paper-white: #f4f4f4;
  }
  * { margin: 0; padding: 0; box-sizing: border-box; }
  html, body {
    width: 1200px;
    height: 576px;
    overflow: hidden;
    background: var(--backdrop);
    font-family: "Poppins", sans-serif;
  }
  .stage {
    position: relative;
    width: 1200px;
    height: 576px;
  }
  .card {
    position: absolute;
    top: 138px;
    height: 292px;
    border-radius: 10px;
  }
  .card-front {
    left: 102px;
    width: 486px;
    background: linear-gradient(180deg, var(--card-dark-edge) 0%, var(--card-dark) 100%);
  }
  .card-back {
    left: 596px;
    width: 480px;
    height: 290px;
    background: var(--card-light);
  }
  .front-wordmark {
    position: absolute;
    left: 48px;
    top: 126px;
    display: flex;
    align-items: center;
    gap: 12px;
  }
  .wordmark-text {
    font-weight: 800;
    font-size: 30px;
    letter-spacing: 1px;
    color: var(--paper-white);
    text-transform: uppercase;
    line-height: 1;
  }
  .wordmark-mark {
    width: 12px;
    height: 12px;
    background: var(--accent);
  }
  .person {
    position: absolute;
    right: 30px;
    top: 30px;
    text-align: right;
  }
  .person-name {
    font-weight: 600;
    font-size: 22px;
    color: var(--accent);
    line-height: 1.2;
  }
  .person-title {
    font-size: 12px;
    color: var(--ink);
    margin-top: 2px;
  }
  .back-wordmark {
    position: absolute;
    left: 32px;
    top: 228px;
    font-weight: 800;
    font-size: 24px;
    color: var(--ink);
    text-transform: uppercase;
    letter-spacing: 0.5px;
    line-height: 1;
  }
  .contact-list {
    position: absolute;
    right: 28px;
    top: 214px;
    list-style: none;
    text-align: right;
  }
  .contact-item {
    display: flex;
    justify-content: flex-end;
    align-items: center;
    gap: 7px;
    font-size: 12px;
    color: var(--ink-soft);
    line-height: 17px;
  }
  .contact-icon {
    width: 10px;
    height: 10px;
    fill: var(--accent);
  }
</style>
</head>
<body>
<main class="stage">
  <section class="card card-front" aria-label="Card front">
    <div class="front-wordmark">
      <span class="wordmark-text">Ridgemont Build</span>
      <span class="wordmark-mark"></span>
    </div>
  </section>

  <section class="card card-back" aria-label="Card back">
    <div class="person">
      <p class="person-name">Tomas Reyes</p>
      <p class="person-title">Director</p>
    </div>

    <p class="back-wordmark">Ridgemont Build</p>

    <ul class="contact-list">
      <li class="contact-item">004-555-0147
        <svg class="contact-icon" viewBox="0 0 10 10" aria-hidden="true"><path d="M1 3.5C1 2 2.5 1.5 5 1.5S9 2 9 3.5L7.5 4 7 3H3L2.5 4z"/><rect x="2" y="5" width="6" height="4" rx="1"/></svg>
      </li>
      <li class="contact-item">tomas@ridgemont.com
        <svg class="contact-icon" viewBox="0 0 10 10" aria-hidden="true"><rect x="0.5" y="2" width="9" height="6.5" rx="0.5"/><path d="M0.8 2.3 5 5.6 9.2 2.3" fill="none" stroke="#f1f1f0" stroke-width="0.9"/></svg>
      </li>
      <li class="contact-item">www.ridgemont.com
        <svg class="contact-icon" viewBox="0 0 10 10" aria-hidden="true"><circle cx="5" cy="5" r="4.5"/><path d="M0.5 5h9M5 0.5c-2.2 2.5-2.2 6.5 0 9M5 0.5c2.2 2.5 2.2 6.5 0 9" fill="none" stroke="#f1f1f0" stroke-width="0.7"/></svg>
      </li>
    </ul>
  </section>
</main>
</body>
</html>
```